Business Card for Polygraph business in Africa

Business Card . Polygraph Examiner based in Tanzania, East Africa.
Business Card will be used to disseminate contact information to potential clients.
It should convey that I am a professional specifically in the polygraph field and perform my work with integrity.

I have attached the business card that I'm currently using, which I threw together myself initially. It's not professional enough.

Target Market(s)

Banks, Accounting Firms, Government Ministries, Gas, Oil, & Gemstone Mining Concerns, Wildlife Conservation NGOs, International companies located in East Africa.

Industry/Entity Type

Business

Contact Information for Business Card

Veritrace Kilonga
Miriam Holloway
PO Box 48317
Arusha, Tanzania
+255 612 839 274
miriamholloway@postvale.example

Colors
00a990
f37122
faa54b

Requirements
Must have
• - Veritrace Kilonga (with the word "Polygraph" being more prominent than the word "Tanzania")
• - Forensic Examinations
• - Employment Screening
• - Should contain a logo of the Continental Truthline Society (of which I'm a member)
• - I would like an accent design (such as the polygraph "squiggles" of a cardio tracing or such as that)
• - My contact information (less prominent, but large enough to read legibly). I would also consider putting the contact information on the second side of the card.
Nice to have
• My color suggestions are changeable.
Should not have
• Anything "cutesy" or "cartoonish"

```html
<!DOCTYPE html>
<html lang="en">
<head>
<meta charset="utf-8">
<title>Veritrace Kilonga – Business Card</title>
<link rel="stylesheet" href="https://fonts.googleapis.com/css2?family=Roboto:wght@300;400;700&display=swap">
<style>
  :root {
    --page: #e9e7e3;
    --card: #ffffff;
    --brand-blue: #1b4fa6;
    --text-grey: #6f6f6f;
    --rule-grey: #9a9a9a;
    --edge-grey: #6a6a6a;
    --badge-ring: #3a4fa0;
  }
  * { box-sizing: border-box; margin: 0; padding: 0; }
  html, body { width: 1200px; height: 886px; overflow: hidden; }
  body {
    background: var(--page);
    font-family: "Roboto", Arial, sans-serif;
    position: relative;
  }
  .card {
    position: absolute;
    top: 288px;
    width: 540px;
    height: 310px;
    background: var(--card);
    border-radius: 18px;
    box-shadow: 0 6px 18px rgba(0,0,0,0.18);
    overflow: hidden;
  }
  .card--front { left: 40px; }
  .card--back { left: 620px; }

  /* front */
  .brand {
    position: absolute; left: 44px; top: 42px;
    display: flex; align-items: center; gap: 10px;
  }
  .brand__dot {
    width: 18px; height: 18px; border-radius: 50%;
    background: var(--brand-blue);
  }
  .brand__name {
    font-weight: 700; font-size: 25px; letter-spacing: 0.5px;
    color: var(--brand-blue);
  }
  .brand__rule {
    position: absolute; left: 72px; top: 80px; width: 300px;
    border-top: 1.5px solid var(--rule-grey);
  }
  .brand__tagline {
    position: absolute; left: 72px; top: 86px;
    font-size: 10.5px; letter-spacing: 0.4px; color: var(--text-grey);
    text-transform: uppercase;
  }
  .person {
    position: absolute; left: 300px; top: 122px;
  }
  .person__name {
    font-weight: 700; font-size: 19px; color: var(--brand-blue);
    text-transform: uppercase; letter-spacing: 0.3px;
  }
  .person__company {
    font-weight: 300; font-size: 14px; color: var(--text-grey);
    text-transform: uppercase; letter-spacing: 0.6px; margin-top: 2px;
  }
  .address {
    position: absolute; left: 395px; top: 178px;
    font-size: 13px; line-height: 18px; color: #444;
  }
  .member-badge {
    position: absolute; left: 30px; top: 200px;
    width: 56px; height: 56px; border-radius: 50%;
    border: 3px solid var(--badge-ring);
    background: #eef0f8;
  }
  .contact {
    position: absolute; left: 170px; top: 212px;
    font-size: 13px; line-height: 20px; color: #333;
    list-style: none;
  }
  .contact li { display: flex; align-items: center; gap: 8px; }
  .contact svg { width: 11px; height: 11px; fill: var(--brand-blue); }
  .edge-band {
    position: absolute; left: 0; bottom: 0; width: 100%; height: 30px;
  }
  .edge-band__web {
    position: absolute; right: 22px; bottom: 7px;
    font-size: 12.5px; color: #fff; letter-spacing: 0.2px;
  }

  /* back */
  .back-brand {
    position: absolute; left: 0; right: 0; top: 112px;
    display: flex; justify-content: center; align-items: center; gap: 12px;
  }
  .back-brand__dot {
    width: 30px; height: 30px; border-radius: 50%;
    border: 3px solid var(--rule-grey);
  }
  .back-brand__name {
    font-weight: 700; font-size: 34px; color: var(--brand-blue);
  }
  .back-rule {
    position: absolute; left: 130px; right: 90px; top: 168px;
    border-top: 1.5px solid var(--rule-grey);
  }
  .back-tagline {
    position: absolute; left: 0; right: 0; top: 180px; text-align: center;
    font-size: 13px; color: #333; letter-spacing: 0.3px;
  }
</style>
</head>
<body>

<section class="card card--front">
  <div class="brand">
    <span class="brand__dot"></span>
    <span class="brand__name">VERITRACE KILONGA</span>
  </div>
  <div class="brand__rule"></div>
  <p class="brand__tagline">Forensic Examinations • Employment Screening</p>

  <div class="person">
    <p class="person__name">Miriam Holloway</p>
    <p class="person__company">Veritrace Kilonga</p>
  </div>

  <p class="address">PO Box 48317<br>Arusha, Tanzania</p>

  <div class="member-badge" role="img" aria-label="Continental Truthline Society membership badge"></div>

  <ul class="contact">
    <li>
      <svg viewBox="0 0 24 24"><path d="M6.6 10.8a15.1 15.1 0 0 0 6.6 6.6l2.2-2.2a1 1 0 0 1 1-.25 11.4 11.4 0 0 0 3.6.57 1 1 0 0 1 1 1V20a1 1 0 0 1-1 1A17 17 0 0 1 3 4a1 1 0 0 1 1-1h3.5a1 1 0 0 1 1 1c0 1.25.2 2.45.57 3.6a1 1 0 0 1-.25 1z"/></svg>
      +255 612 839 274
    </li>
    <li>
      <svg viewBox="0 0 24 24"><path d="M2 5h20v14H2z M2 5l10 8 10-8" /></svg>
      miriamholloway@postvale.example
    </li>
  </ul>

  <svg class="edge-band" viewBox="0 0 540 30" preserveAspectRatio="none">
    <rect x="0" y="14" width="300" height="16" fill="var(--edge-grey)"/>
    <polygon points="300,0 540,0 540,30 288,30" fill="var(--brand-blue)"/>
  </svg>
  <span class="edge-band__web">www.miriamholloway.example</span>
</section>

<section class="card card--back">
  <div class="back-brand">
    <span class="back-brand__dot"></span>
    <span class="back-brand__name">Veritrace Kilonga</span>
  </div>
  <div class="back-rule"></div>
  <p class="back-tagline">Forensic Examinations • Employment Screening</p>
</section>

</body>
</html>
```